Brochure for a civil enineering company in A4 format

I need a brochure design for our company TIRO Engineering S.r.l.. We are an engineering consultant company. Our main clients are from the infrastructure industry (geotechnical and underground sectors mainly).
We are looking for a 2 pages (4 faces) fold out design with a glued pocket where we can put individual data sheets.
I need A4 format pages.

Target Market(s)

We are an engineering consultant company. Our main clients are from the infrastructure industry (geotechnical and underground sectors mainly).

Industry/Entity Type

Civil Engineer

Font styles to use
Sans Serif

Requirements
Must have
• Overall: 2 pages in A4 format
Essential style. Bright and modern appearance.
Glued pocket
Logo integrated in a picture on the pocket where I would like to insert a slogan (… tiro engineering … reliable solutions …)
Attached are selected images which the designer can use and edit at their own discretion.
Some advice in the following (anyway designers are free to provide their solutions):
Outer sheets:
Front page with name, logo. It could be nice to have the “m” of the logo integrated in a pictures, also a modified picture (I mean modify one of the attached pictures) so to create a general image and do not tie the cover to a specific job.
Back page: offices address and contact email address. Nice to have one space for a slogan.
Inner sheet: text that I upload in the file “inside-sheets”, possibly with pictures on each sheet. In the right faces insert the glued pocket. On this pages insert the section OUR EXPERIENCE ….with a space for a picture of our team.
Nice to have
• Clean and essential design.
Pictures choosing from the atteched ones. Pictures could be modified in a very light manner to make them a general idea of the work ( I mean geotechnical world) without to be immediately linked to a specific site.
Should not have
• excessive frills

```html
<!DOCTYPE html>
<html lang="en">
<head>
<meta charset="UTF-8">
<title>TIRO Engineering – Brochure Spreads</title>
<link href="https://fonts.googleapis.com/css2?family=Poppins:wght@400;500;600;700&family=Open+Sans:wght@400;600&display=swap" rel="stylesheet">
<style>
  :root{
    --bg:#e9ecee;
    --paper:#ffffff;
    --ink:#1d1d1f;
    --text:#555a60;
    --muted:#8b9096;
    --accent:#1a1a1a;
    --photo-site-a:#8d8a80;
    --photo-site-b:#c9c2b3;
    --photo-tunnel-a:#3e3a35;
    --photo-tunnel-b:#8a8174;
    --photo-team-a:#e4e6e9;
    --photo-team-b:#6d7684;
  }
  *{box-sizing:border-box;margin:0;padding:0}
  html,body{width:672px;height:1200px;overflow:hidden}
  body{background:var(--bg);font-family:"Open Sans",Arial,sans-serif;color:var(--text);position:relative}

  .spread{position:absolute;left:20px;width:632px;height:360px;background:var(--paper);
    box-shadow:0 6px 18px rgba(0,0,0,.15);overflow:hidden}
  .spread--outer{top:160px}
  .spread--inner{top:620px}
  .fold{position:absolute;top:0;bottom:0;width:1px;background:rgba(0,0,0,.06)}

  /* outer spread */
  .outer-art{position:absolute;inset:0}
  .wordmark{font-family:"Poppins",Arial,sans-serif;font-weight:600;color:var(--ink);
    letter-spacing:-.5px;display:flex;align-items:center;gap:5px;line-height:1}
  .wordmark__dot{width:7px;height:7px;border-radius:50%;background:var(--ink)}
  .back-contact{position:absolute;left:240px;top:100px;width:70px;text-align:left}
  .back-contact .wordmark{font-size:20px;margin-bottom:14px}
  .contact-label{font-family:"Poppins",Arial,sans-serif;font-weight:600;font-size:6px;color:var(--ink);letter-spacing:.6px;margin:8px 0 3px}
  .contact-line{font-size:5.5px;line-height:1.6}
  .cover-mark{position:absolute;left:392px;top:80px}
  .cover-mark .wordmark{font-size:34px}

  /* inner spread */
  .inner-grid{position:absolute;inset:0;display:grid;grid-template-columns:200px 216px 216px}
  .panel{position:relative;padding:0 16px}
  .photo{background:linear-gradient(135deg,var(--a),var(--b))}
  .panel--company .photo{position:absolute;left:0;top:0;width:200px;height:150px;
    --a:var(--photo-tunnel-a);--b:var(--photo-tunnel-b);border-bottom-right-radius:80px 40px}
  .panel--company .body{position:absolute;left:16px;top:172px;width:165px}
  .corner-band{position:absolute;left:-30px;bottom:-40px;width:200px;height:80px;background:var(--accent);border-radius:50%}
  h2{font-family:"Poppins",Arial,sans-serif;font-weight:600;font-size:9px;color:var(--ink);letter-spacing:.4px;margin-bottom:6px}
  p{font-size:6.2px;line-height:1.65;margin-bottom:5px}
  .panel--services{padding-top:20px}
  .services{list-style:none;margin-top:4px}
  .services li{display:flex;align-items:center;gap:6px;font-size:6.2px;margin-bottom:7px}
  .services svg{flex:none}
  .circles{position:absolute;left:16px;right:16px;bottom:18px;height:120px}
  .circle{position:absolute;border-radius:50%;border:2px solid var(--paper);
    --a:var(--photo-tunnel-a);--b:var(--photo-tunnel-b)}
  .circle--1{left:0;top:12px;width:56px;height:56px}
  .circle--2{left:62px;top:0;width:48px;height:48px;--a:#6f6a62;--b:#b4ab9c}
  .circle--3{left:116px;top:6px;width:60px;height:60px}
  .circle--4{left:56px;top:52px;width:70px;height:70px;--a:#4d4842;--b:#a89d8d}
  .panel--expertise{padding:0}
  .panel--expertise .photo{height:140px;--a:var(--photo-team-a);--b:var(--photo-team-b)}
  .panel--expertise .body{padding:14px 16px 0}
</style>
</head>
<body>

<section class="spread spread--outer" aria-label="Outer pages: back and front cover">
  <svg class="outer-art" viewBox="0 0 632 360" width="632" height="360">
    <defs>
      <linearGradient id="site" x1="0" y1="0" x2="1" y2="1">
        <stop offset="0" stop-color="var(--photo-site-a)"/>
        <stop offset="1" stop-color="var(--photo-site-b)"/>
      </linearGradient>
    </defs>
    <path role="img" aria-label="Photo of a geotechnical construction site" fill="url(#site)"
      d="M0 0 H150 C205 60 205 300 150 360 H0 Z"/>
    <path role="img" aria-label="Photo of an excavation and foundation works site" fill="url(#site)"
      d="M632 0 H500 C445 70 445 290 500 360 H632 Z"/>
  </svg>
  <div class="fold" style="left:316px"></div>

  <div class="back-contact">
    <div class="wordmark"><span class="wordmark__dot"></span>tiro</div>
    <div class="contact-label">OUR OFFICES</div>
    <div class="contact-line">Via Lago 14</div>
    <div class="contact-line">20121 Milano, Italy</div>
    <div class="contact-line">+39 02 0000 0000</div>
    <div class="contact-label">CONTACT US</div>
    <div class="contact-line">info@tiroeng.example</div>
    <div class="contact-line">www.tiroeng.example</div>
  </div>

  <div class="cover-mark">
    <div class="wordmark"><span class="wordmark__dot"></span>tiro</div>
  </div>
</section>

<section class="spread spread--inner" aria-label="Inner pages">
  <div class="inner-grid">
    <div class="panel panel--company">
      <div class="photo" role="img" aria-label="Photo of a tunnel under construction"></div>
      <div class="body">
        <h2>OUR COMPANY</h2>
        <p>TIRO Engineering S.r.l. is an engineering consultancy serving the infrastructure industry. We support owners, contractors and designers in geotechnical and underground works, from early studies to site assistance, with clear methods and reliable solutions.</p>
      </div>
      <div class="corner-band"></div>
    </div>

    <div class="panel panel--services">
      <h2>OUR SERVICES</h2>
      <p>We deliver design and consulting services across every stage of underground and geotechnical projects.</p>
      <ul class="services">
        <li><svg width="7" height="7" viewBox="0 0 7 7"><circle cx="3.5" cy="3.5" r="3.5" fill="#1a1a1a"/></svg>Tunnel design and excavation analysis</li>
        <li><svg width="7" height="7" viewBox="0 0 7 7"><circle cx="3.5" cy="3.5" r="3.5" fill="#1a1a1a"/></svg>Geotechnical investigation and monitoring</li>
        <li><svg width="7" height="7" viewBox="0 0 7 7"><circle cx="3.5" cy="3.5" r="3.5" fill="#1a1a1a"/></svg>Foundations, retaining walls and slopes</li>
        <li><svg width="7" height="7" viewBox="0 0 7 7"><circle cx="3.5" cy="3.5" r="3.5" fill="#1a1a1a"/></svg>Site assistance and construction support</li>
      </ul>
      <div class="circles">
        <div class="circle circle--1 photo" role="img" aria-label="Photo of a tunnel boring machine"></div>
        <div class="circle circle--2 photo" role="img" aria-label="Photo of a drilling rig on site"></div>
        <div class="circle circle--3 photo" role="img" aria-label="Photo of a tunnel lining"></div>
        <div class="circle circle--4 photo" role="img" aria-label="Photo of an underground gallery"></div>
      </div>
    </div>

    <div class="panel panel--expertise">
      <div class="photo" role="img" aria-label="Photo of the engineering team"></div>
      <div class="body">
        <h2>OUR EXPERTISE AND EXPERIENCE</h2>
        <p>Our team combines long field experience with advanced numerical modelling. Engineers work side by side with clients to turn complex ground conditions into safe, efficient and durable structures.</p>
        <p>Over the years we have taken part in major road, rail and metro projects, gaining a deep knowledge of mechanized and conventional tunnelling.</p>
        <p>Each project is followed by a dedicated team from the first study to final delivery.</p>
      </div>
    </div>
  </div>
  <div class="fold" style="left:200px"></div>
  <div class="fold" style="left:416px"></div>
</section>

</body>
</html>
```